Restaurant promotion flyer

I am selling restaurant thermal paper, pizza boxes, show-up: Order online local delivery, Competitive price,

Target Market(s)

Restaurants

Industry/Entity Type

Restaurant supplies

Requirements
Must have
• The flyers should have headers saying local, the pictures of the items we are selling, and the pricing right next to each of them. The flyer should also be attractive to customers.
Nice to have
• Somethings nice is can show how low and good the pricing is for the products.
Should not have
• Receipt Paper $45.00 3-1/8x230-50 R ; $35.00 3-1/8X119-50 R; Credit Card Paper $26.00 2-1/4x50-100 R; $16.00 2-1/4x85-50 R; Pump Gas Station: $31.00 2-5/16x356-24 R ; $ 25.00 2-5/16X210-24 R;

```html
<!DOCTYPE html>
<html lang="en">
<head>
<meta charset="utf-8">
<title>Restaurant Supplies Promotion Flyer</title>
<link href="https://fonts.googleapis.com/css2?family=Nunito+Sans:wght@700;800;900&family=Open+Sans:wght@400;600;700;800&family=Barlow+Condensed:ital,wght@1,800&display=swap" rel="stylesheet">
<style>
  :root {
    --red: #d71f26;
    --footer-red: #cc2229;
    --wine: #6e1016;
    --lime: #19ff00;
    --white: #ffffff;
    --ink: #111111;
    --paper: #ffffff;
    --label-tone-a: #f4f4f2;
    --label-tone-b: #cfcfcc;
    --kraft-a: #d9b07a;
    --kraft-b: #a87844;
    --cup-a: #fbfbf9;
    --cup-b: #d8d8d4;
  }
  * { box-sizing: border-box; margin: 0; padding: 0; }
  html, body { width: 1200px; height: 1200px; overflow: hidden; background: var(--paper); }
  .flyer {
    position: absolute; left: 136px; top: 0;
    width: 928px; height: 1200px;
    background: var(--white);
    display: flex; flex-direction: column;
    font-family: "Open Sans", sans-serif;
  }
  .masthead {
    height: 267px; background: var(--red); color: var(--white);
    text-align: center; font-family: "Nunito Sans", sans-serif;
    padding-top: 42px;
  }
  .masthead-title { font-size: 104px; font-weight: 900; line-height: 0.95; letter-spacing: 1px; }
  .masthead-subtitle { font-size: 60px; font-weight: 900; line-height: 1.05; letter-spacing: 1px; }
  .masthead-tagline { font-family: "Open Sans", sans-serif; font-size: 20px; font-weight: 700; margin-top: 6px; }

  .offer-band { position: relative; height: 58px; background: var(--wine); }
  .offer-band svg { position: absolute; left: 0; top: 0; }
  .offer-band-flag {
    position: absolute; left: 14px; top: 6px;
    font-family: "Barlow Condensed", sans-serif; font-style: italic; font-weight: 800;
    font-size: 21px; line-height: 23px; color: var(--wine);
  }
  .offer-band-headline {
    position: absolute; left: 276px; right: 12px; top: 0; height: 58px;
    display: flex; align-items: center; justify-content: center;
    font-family: "Nunito Sans", sans-serif; font-weight: 900; font-size: 26px;
    color: var(--white); letter-spacing: 0.5px; white-space: nowrap;
  }

  .product-grid {
    height: 792px;
    display: grid; grid-template-columns: repeat(3, 1fr); grid-template-rows: repeat(4, 1fr);
    padding: 16px 0 8px;
  }
  .product { position: relative; }
  .product-photo { position: absolute; border-radius: 6px; }
  .photo-labels { left: 128px; top: 25px; width: 148px; height: 128px;
    background: linear-gradient(135deg, var(--label-tone-a), var(--label-tone-b)); }
  .photo-boxes { left: 130px; top: 28px; width: 170px; height: 122px;
    background: linear-gradient(135deg, var(--kraft-a), var(--kraft-b)); }
  .photo-cups { left: 138px; top: 20px; width: 148px; height: 130px;
    background: linear-gradient(135deg, var(--cup-a), var(--cup-b)); }
  .product-info { position: absolute; left: 26px; top: 12px; color: var(--ink); }
  .badge {
    display: inline-block; background: var(--red); color: var(--white);
    font-size: 12px; font-weight: 600; padding: 0 3px; line-height: 16px;
  }
  .price { font-weight: 800; font-size: 40px; line-height: 38px; letter-spacing: -1px; }
  .price sup { font-size: 18px; vertical-align: 16px; letter-spacing: 0; }
  .price .currency { font-size: 20px; vertical-align: 12px; }
  .price-note { font-size: 10px; line-height: 10px; color: #333; }
  .product-name { font-size: 17px; font-weight: 700; line-height: 16px; margin-top: 12px; }
  .product-tag { font-size: 12px; font-weight: 800; line-height: 12px; }
  .product-copy { font-size: 10.5px; line-height: 10.5px; margin-top: 2px; }

  .footer {
    height: 83px; background: var(--footer-red); color: var(--white);
    display: flex; align-items: center;
  }
  .footer-brand { width: 327px; text-align: center; font-family: "Nunito Sans", sans-serif; font-weight: 900; }
  .footer-brand-name { font-size: 32px; line-height: 30px; letter-spacing: 0.5px; }
  .footer-brand-tag { font-size: 13px; line-height: 14px; }
  .footer-copy { font-size: 16px; line-height: 22px; }
  .footer-copy .lead { font-weight: 700; }
  .footer-copy .mid { font-weight: 600; }
  .footer-copy .tail { font-weight: 400; font-size: 14px; }
</style>
</head>
<body>
<main class="flyer">
  <header class="masthead">
    <h1 class="masthead-title">LOREM IPSUM</h1>
    <h2 class="masthead-subtitle">CONSECTETUR ADIPISCING</h2>
    <p class="masthead-tagline">LOREM IPSUM DOLOR SIT AMET, CONSECTETUR ADIPISCING ELIT</p>
  </header>

  <section class="offer-band">
    <svg width="276" height="58" viewBox="0 0 276 58" aria-hidden="true">
      <polygon points="0,0 255,0 240,58 0,58" fill="var(--lime)"/>
      <polygon points="258,0 264,0 249,58 243,58" fill="var(--white)"/>
    </svg>
    <div class="offer-band-flag">LOREM IPSUM<br>CONSECTETUR ADIPISCING ELIT</div>
    <div class="offer-band-headline">LOREM IPSUM CONSECTETUR ADIPISCING ELIT</div>
  </section>

  <section class="product-grid">
    <article class="product">
      <div class="product-photo photo-labels" role="img" aria-label="Thermal label and receipt paper rolls"></div>
      <div class="product-info">
        <span class="badge">QUALIFIED</span>
        <div class="price"><span class="currency">$</span>00<sup>00</sup></div>
        <div class="price-note">best prices</div>
        <div class="product-name">LOREM IPSUM</div>
        <div class="product-tag">DOLOR SIT AMET,</div>
        <p class="product-copy">consectetur adipiscing elit,<br>sed do eiusmod tempor<br>incididunt ut<br>labore et dolore<br>magna aliqua.</p>
      </div>
    </article>
    <article class="product">
      <div class="product-photo photo-boxes" role="img" aria-label="Open kraft pizza box"></div>
      <div class="product-info">
        <span class="badge">QUALIFIED</span>
        <div class="price"><span class="currency">$</span>00<sup>00</sup></div>
        <div class="price-note">best prices</div>
        <div class="product-name">LOREM IPSUM</div>
        <div class="product-tag">DOLOR SIT AMET,</div>
        <p class="product-copy">consectetur adipiscing elit,<br>sed do eiusmod tempor<br>incididunt ut<br>labore et dolore<br>magna aliqua.</p>
      </div>
    </article>
    <article class="product">
      <div class="product-photo photo-cups" role="img" aria-label="White paper cups with lids"></div>
      <div class="product-info">
        <span class="badge">QUALIFIED</span>
        <div class="price"><span class="currency">$</span>00<sup>00</sup></div>
        <div class="price-note">best prices</div>
        <div class="product-name">LOREM IPSUM</div>
        <div class="product-tag">DOLOR SIT AMET,</div>
        <p class="product-copy">consectetur adipiscing elit,<br>sed do eiusmod tempor<br>incididunt ut<br>labore et dolore<br>magna aliqua.</p>
      </div>
    </article>

    <article class="product">
      <div class="product-photo photo-boxes" role="img" aria-label="Open kraft pizza box"></div>
      <div class="product-info">
        <span class="badge">QUALIFIED</span>
        <div class="price"><span class="currency">$</span>00<sup>00</sup></div>
        <div class="price-note">best prices</div>
        <div class="product-name">LOREM IPSUM</div>
        <div class="product-tag">DOLOR SIT AMET,</div>
        <p class="product-copy">consectetur adipiscing elit,<br>sed do eiusmod tempor<br>incididunt ut<br>labore et dolore<br>magna aliqua.</p>
      </div>
    </article>
    <article class="product">
      <div class="product-photo photo-cups" role="img" aria-label="White paper cups with lids"></div>
      <div class="product-info">
        <span class="badge">QUALIFIED</span>
        <div class="price"><span class="currency">$</span>00<sup>00</sup></div>
        <div class="price-note">best prices</div>
        <div class="product-name">LOREM IPSUM</div>
        <div class="product-tag">DOLOR SIT AMET,</div>
        <p class="product-copy">consectetur adipiscing elit,<br>sed do eiusmod tempor<br>incididunt ut<br>labore et dolore<br>magna aliqua.</p>
      </div>
    </article>
    <article class="product">
      <div class="product-photo photo-labels" role="img" aria-label="Thermal label and receipt paper rolls"></div>
      <div class="product-info">
        <span class="badge">QUALIFIED</span>
        <div class="price"><span class="currency">$</span>00<sup>00</sup></div>
        <div class="price-note">best prices</div>
        <div class="product-name">LOREM IPSUM</div>
        <div class="product-tag">DOLOR SIT AMET,</div>
        <p class="product-copy">consectetur adipiscing elit,<br>sed do eiusmod tempor<br>incididunt ut<br>labore et dolore<br>magna aliqua.</p>
      </div>
    </article>

    <article class="product">
      <div class="product-photo photo-cups" role="img" aria-label="White paper cups with lids"></div>
      <div class="product-info">
        <span class="badge">QUALIFIED</span>
        <div class="price"><span class="currency">$</span>00<sup>00</sup></div>
        <div class="price-note">best prices</div>
        <div class="product-name">LOREM IPSUM</div>
        <div class="product-tag">DOLOR SIT AMET,</div>
        <p class="product-copy">consectetur adipiscing elit,<br>sed do eiusmod tempor<br>incididunt ut<br>labore et dolore<br>magna aliqua.</p>
      </div>
    </article>
    <article class="product">
      <div class="product-photo photo-labels" role="img" aria-label="Thermal label and receipt paper rolls"></div>
      <div class="product-info">
        <span class="badge">QUALIFIED</span>
        <div class="price"><span class="currency">$</span>00<sup>00</sup></div>
        <div class="price-note">best prices</div>
        <div class="product-name">LOREM IPSUM</div>
        <div class="product-tag">DOLOR SIT AMET,</div>
        <p class="product-copy">consectetur adipiscing elit,<br>sed do eiusmod tempor<br>incididunt ut<br>labore et dolore<br>magna aliqua.</p>
      </div>
    </article>
    <article class="product">
      <div class="product-photo photo-boxes" role="img" aria-label="Open kraft pizza box"></div>
      <div class="product-info">
        <span class="badge">QUALIFIED</span>
        <div class="price"><span class="currency">$</span>00<sup>00</sup></div>
        <div class="price-note">best prices</div>
        <div class="product-name">LOREM IPSUM</div>
        <div class="product-tag">DOLOR SIT AMET,</div>
        <p class="product-copy">consectetur adipiscing elit,<br>sed do eiusmod tempor<br>incididunt ut<br>labore et dolore<br>magna aliqua.</p>
      </div>
    </article>

    <article class="product">
      <div class="product-photo photo-labels" role="img" aria-label="Thermal label and receipt paper rolls"></div>
      <div class="product-info">
        <span class="badge">QUALIFIED</span>
        <div class="price"><span class="currency">$</span>00<sup>00</sup></div>
        <div class="price-note">best prices</div>
        <div class="product-name">LOREM IPSUM</div>
        <div class="product-tag">DOLOR SIT AMET,</div>
        <p class="product-copy">consectetur adipiscing elit,<br>sed do eiusmod tempor<br>incididunt ut<br>labore et dolore<br>magna aliqua.</p>
      </div>
    </article>
    <article class="product">
      <div class="product-photo photo-boxes" role="img" aria-label="Open kraft pizza box"></div>
      <div class="product-info">
        <span class="badge">QUALIFIED</span>
        <div class="price"><span class="currency">$</span>00<sup>00</sup></div>
        <div class="price-note">best prices</div>
        <div class="product-name">LOREM IPSUM</div>
        <div class="product-tag">DOLOR SIT AMET,</div>
        <p class="product-copy">consectetur adipiscing elit,<br>sed do eiusmod tempor<br>incididunt ut<br>labore et dolore<br>magna aliqua.</p>
      </div>
    </article>
    <article class="product">
      <div class="product-photo photo-labels" role="img" aria-label="Thermal label and receipt paper rolls"></div>
      <div class="product-info">
        <span class="badge">QUALIFIED</span>
        <div class="price"><span class="currency">$</span>00<sup>00</sup></div>
        <div class="price-note">best prices</div>
        <div class="product-name">LOREM IPSUM</div>
        <div class="product-tag">DOLOR SIT AMET,</div>
        <p class="product-copy">consectetur adipiscing elit,<br>sed do eiusmod tempor<br>incididunt ut<br>labore et dolore<br>magna aliqua.</p>
      </div>
    </article>
  </section>

  <footer class="footer">
    <div class="footer-brand">
      <div class="footer-brand-name">LOREM IPSUM</div>
      <div class="footer-brand-tag">CONSECTETUR ADIPISCING ELIT</div>
    </div>
    <div class="footer-copy">
      <div class="lead">LOREM IPSUM DOLOR SIT AMET,</div>
      <div class="mid">consectetur adipiscing elit, sed do eiusmod tempor incididunt ut</div>
      <div class="tail">labore et dolore magna aliqua. Ut enim ad minim veniam,</div>
    </div>
  </footer>
</main>
</body>
</html>
```